Web Developer Needs a Business Card Design

I need a personal business card design that represents me as a web developer for potential employers. I would like the background to be a dark color on the front for contrast with my logo and name. The back will have all my information along with a smaller version of the logo. I want something with a modern look and feel, not too conservative. This will be used for potential employers and freelance work.

Industry/Entity Type

Business

Contact Information for Business Card

Front should have my logo and name. The back should have all my personal information which would include: name: Tom Varulek, phone: 570-614-3098, email: tomvarulek@quillbox.net, website url: www.tomvarulek.net, logo, web developer.

Font styles to use
Sans Serif

Requirements
Must have
• Must include my logo. The color palette base color will be the logo color.

```html
<!DOCTYPE html>
<html lang="en">
<head>
<meta charset="utf-8">
<title>Tom Varulek — Business Card</title>
<link rel="stylesheet" href="https://fonts.googleapis.com/css2?family=Lato:wght@400;700&display=swap">
<style>
  :root {
    --page: #e8e8e8;
    --card-light: #3b8c7b;
    --card-dark: #1e6b58;
    --ink: #ffffff;
    --ink-soft: rgba(255, 255, 255, 0.92);
  }
  * { margin: 0; padding: 0; box-sizing: border-box; }
  html, body {
    width: 1200px;
    height: 720px;
    overflow: hidden;
    background: var(--page);
    font-family: "Lato", sans-serif;
    color: var(--ink);
  }
  .card-pair {
    position: absolute;
    left: 74px;
    top: 212px;
    display: flex;
    gap: 12px;
  }
  .card {
    position: relative;
    width: 520px;
    height: 296px;
    border-radius: 8px;
    overflow: hidden;
    background: linear-gradient(160deg, var(--card-light) 0%, var(--card-dark) 100%);
  }
  .split-disc {
    position: absolute;
    top: 0;
    width: 520px;
    height: 296px;
  }
  .card--back .split-disc { left: 0; }
  .card--front .split-disc { left: 0; }

  .brand {
    position: absolute;
    left: 31px;
    top: 31px;
    display: flex;
    align-items: center;
    gap: 12px;
  }
  .brand-mark {
    width: 60px;
    height: 60px;
    border: 4px solid var(--ink);
    border-radius: 50%;
  }
  .brand-name {
    font-size: 22px;
    font-weight: 400;
    letter-spacing: 2.6px;
    text-transform: uppercase;
  }
  .holder {
    position: absolute;
    left: 33px;
    top: 130px;
  }
  .holder-name {
    font-size: 18px;
    font-weight: 700;
    line-height: 22px;
  }
  .holder-role {
    font-size: 15px;
    line-height: 20px;
    color: var(--ink-soft);
  }
  .contact-list {
    position: absolute;
    left: 31px;
    top: 192px;
    list-style: none;
  }
  .contact-list li {
    display: flex;
    align-items: center;
    gap: 6px;
    font-size: 15px;
    line-height: 20px;
    color: var(--ink-soft);
  }
  .contact-list svg { width: 15px; height: 15px; flex: none; }

  .front-mark {
    position: absolute;
    left: 277px;
    top: 75px;
    width: 148px;
    height: 148px;
    border: 8px solid var(--ink);
    border-radius: 50%;
  }
  .front-url {
    position: absolute;
    left: 0;
    width: 702px;
    top: 234px;
    text-align: center;
    font-size: 15px;
    letter-spacing: 0.8px;
    color: var(--ink-soft);
  }
</style>
</head>
<body>
  <main class="card-pair">
    <section class="card card--back" aria-label="Card back with contact details">
      <svg class="split-disc" viewBox="0 0 520 296" aria-hidden="true">
        <circle cx="526" cy="148" r="145" fill="none" stroke="#ffffff" stroke-width="3"/>
      </svg>

      <div class="brand">
        <span class="brand-mark"></span>
        <span class="brand-name">Tom Varulek</span>
      </div>

      <div class="holder">
        <p class="holder-name">Tom Varulek</p>
        <p class="holder-role">President</p>
      </div>

      <ul class="contact-list">
        <li>
          <svg viewBox="0 0 16 16" aria-hidden="true"><path fill="#fff" d="M3 2h3l1.2 3-1.7 1.1a8 8 0 0 0 4.4 4.4L11 8.8l3 1.2v3a1 1 0 0 1-1 1A11 11 0 0 1 2 3a1 1 0 0 1 1-1z"/></svg>
          570-614-3098
        </li>
        <li>
          <svg viewBox="0 0 16 16" aria-hidden="true"><rect x="1.5" y="3.5" width="13" height="9" fill="none" stroke="#fff" stroke-width="1.4"/><path d="M1.5 3.5 8 9l6.5-5.5" fill="none" stroke="#fff" stroke-width="1.4"/></svg>
          tomvarulek@quillbox.net
        </li>
        <li>
          <svg viewBox="0 0 16 16" aria-hidden="true"><g fill="none" stroke="#fff" stroke-width="1.3"><circle cx="8" cy="8" r="6.3"/><ellipse cx="8" cy="8" rx="2.8" ry="6.3"/><path d="M1.7 8h12.6M2.8 4.8h10.4M2.8 11.2h10.4"/></g></svg>
          www.tomvarulek.net
        </li>
      </ul>
    </section>

    <section class="card card--front" aria-label="Card front">
      <svg class="split-disc" viewBox="0 0 520 296" aria-hidden="true">
        <circle cx="-6" cy="148" r="145" fill="none" stroke="#ffffff" stroke-width="3"/>
      </svg>
      <span class="front-mark" aria-hidden="true"></span>
      <p class="front-url">www.tomvarulek.net</p>
    </section>
  </main>
</body>
</html>
```